Irrigation Business needs their business cards modernised and revamped

I would like to keep my current logo, colours and revamp the format of the card.

I would like the card to be clean yet important.

Im not sure if you include texture but i would like the named logo to be indented into the card etc.

show me something alive and free something thats clinical to the point yet has a feel of achievement. i would like people to go nice card.

Target Market(s)

high end clients, corporate, sports field manger, the guys that make the decisions

Industry/Entity Type

Business

Contact Information for Business Card

nformation to be included

Dean Harlow (Director)
0487305526
dean@kolvat.biz
www.kestonfieldworks.com

instagram logo
google logo
facebook logo

Colors

Designer to choose colors to be used in the design.

Requirements
Nice to have
• indentations a really nice feel to the card good texture

```html
<!DOCTYPE html>
<html lang="en">
<head>
<meta charset="utf-8">
<title>Keston Fieldworks — Business Card</title>
<link href="https://fonts.googleapis.com/css2?family=Roboto:wght@400;700&family=Roboto+Condensed:wght@400;700&display=swap" rel="stylesheet">
<style>
  :root {
    --backdrop: #1f1f1f;
    --sky: #2ba0cf;
    --navy: #2f63ad;
    --paper: #f1f1f1;
    --field: #2a9d58;
    --white: #ffffff;
  }
  * { margin: 0; padding: 0; box-sizing: border-box; }
  html, body { width: 1200px; height: 960px; overflow: hidden; }
  body {
    background: var(--backdrop);
    font-family: "Roboto", Arial, sans-serif;
    position: relative;
  }
  .card {
    position: absolute;
    width: 600px;
    height: 343px;
    overflow: hidden;
  }
  .card--front { left: 314px; top: 113px; background: var(--paper); }
  .card--back { left: 311px; top: 472px; background: var(--field); }

  .front-shape { position: absolute; inset: 0; }

  .holder {
    position: absolute;
    left: 44px;
    top: 47px;
    color: var(--white);
  }
  .holder__name {
    font-family: "Roboto Condensed", Arial, sans-serif;
    font-weight: 700;
    font-size: 22px;
    line-height: 24px;
  }
  .holder__role {
    font-family: "Roboto Condensed", Arial, sans-serif;
    font-size: 15px;
    line-height: 22px;
  }
  .social {
    display: flex;
    gap: 3px;
    margin-top: 8px;
  }
  .social__dot {
    width: 26px; height: 26px;
    border-radius: 50%;
    background: var(--white);
  }

  .contact {
    position: absolute;
    left: 44px;
    top: 241px;
    list-style: none;
    color: var(--white);
    font-size: 14px;
    line-height: 19px;
  }
  .contact li { display: flex; align-items: center; gap: 9px; }
  .contact svg { width: 13px; height: 13px; flex: none; }

  .brand {
    position: absolute;
    text-align: center;
    font-weight: 700;
  }
  .brand__mark { border-radius: 50%; margin: 0 auto; }
  .brand--front { left: 320px; top: 165px; width: 250px; color: var(--navy); }
  .brand--front .brand__mark {
    width: 76px; height: 76px;
    background: var(--navy);
    margin-bottom: 18px;
  }
  .brand--front .brand__name { font-size: 22px; line-height: 24px; }
  .brand--front .brand__sub { font-size: 15px; letter-spacing: 4px; line-height: 20px; }

  .brand--back { left: 0; top: 80px; width: 600px; color: var(--white); }
  .brand--back .brand__mark {
    width: 106px; height: 106px;
    border: 4px solid var(--white);
    margin-bottom: 18px;
  }
  .brand--back .brand__name { font-size: 32px; line-height: 36px; }
  .brand--back .brand__sub { font-size: 20px; letter-spacing: 7px; line-height: 28px; }
</style>
</head>
<body>
  <section class="card card--front" aria-label="Business card front">
    <svg class="front-shape" viewBox="0 0 600 343" width="600" height="343" aria-hidden="true">
      <path d="M0,0 H382 C340,60 271,160 271,230 C271,290 309,330 349,343 H0 Z" fill="var(--navy)"/>
      <path d="M0,0 H376 C334,60 266,160 266,230 C266,290 304,330 344,343 H0 Z" fill="var(--white)"/>
      <path d="M0,0 H372 C330,60 262,160 262,230 C262,290 300,330 340,343 H0 Z" fill="var(--sky)"/>
    </svg>

    <div class="holder">
      <p class="holder__name">DEAN HARLOW</p>
      <p class="holder__role">DIRECTOR</p>
      <div class="social" aria-label="Social profiles">
        <span class="social__dot"></span>
        <span class="social__dot"></span>
        <span class="social__dot"></span>
      </div>
    </div>

    <ul class="contact">
      <li>
        <svg viewBox="0 0 24 24" aria-hidden="true"><path fill="#fff" d="M6.6 10.8a15.1 15.1 0 0 0 6.6 6.6l2.2-2.2a1 1 0 0 1 1-.25 11.4 11.4 0 0 0 3.6.57 1 1 0 0 1 1 1V20a1 1 0 0 1-1 1A17 17 0 0 1 3 4a1 1 0 0 1 1-1h3.5a1 1 0 0 1 1 1c0 1.25.2 2.45.57 3.57a1 1 0 0 1-.25 1z"/></svg>
        0487305526
      </li>
      <li>
        <svg viewBox="0 0 24 24" aria-hidden="true"><path fill="#fff" d="M2 5h20v14H2z"/><path fill="none" stroke="#2ba0cf" stroke-width="2" d="M2 5l10 8 10-8"/></svg>
        dean@kolvat.biz
      </li>
      <li>
        <svg viewBox="0 0 24 24" aria-hidden="true"><circle cx="12" cy="12" r="10" fill="#fff"/><path fill="none" stroke="#2ba0cf" stroke-width="1.6" d="M2 12h20M12 2c3 3 3 17 0 20M12 2c-3 3-3 17 0 20"/></svg>
        kestonfieldworks.com
      </li>
    </ul>

    <div class="brand brand--front">
      <div class="brand__mark"></div>
      <p class="brand__name">KESTON FIELDWORKS</p>
      <p class="brand__sub">SERVICES</p>
    </div>
  </section>

  <section class="card card--back" aria-label="Business card back">
    <div class="brand brand--back">
      <div class="brand__mark"></div>
      <p class="brand__name">KESTON FIELDWORKS</p>
      <p class="brand__sub">SERVICES</p>
    </div>
  </section>
</body>
</html>
```